Business Card Design

WE are looking for a premium quality Business Cards for a Law Firm . Copies of our current business card is attached.

Contact Information for Business Card

xyz

```html
<!DOCTYPE html>
<html lang="en">
<head>
<meta charset="utf-8">
<title>Hartwell Lawyers – Business Card</title>
<link rel="stylesheet" href="https://fonts.googleapis.com/css2?family=Cinzel:wght@600;700&family=Arimo:wght@400;700&display=swap">
<style>
  :root {
    --bg: #e4e4e4;
    --paper: #f7f7f6;
    --green: #0a3b2c;
    --green-deep: #062a1f;
    --green-mid: #0c4432;
    --gold: #b8945a;
    --ink: #1e1e1e;
    --white: #ffffff;
  }
  * { margin: 0; padding: 0; box-sizing: border-box; }
  html, body { width: 1200px; height: 1200px; overflow: hidden; }
  body {
    background: var(--bg);
    font-family: "Arimo", Arial, sans-serif;
    position: relative;
  }
  .card {
    position: absolute;
    left: 200px;
    width: 800px;
    height: 457px;
    border-radius: 22px;
    overflow: hidden;
  }
  .card-front { top: 90px; background: var(--paper); }
  .card-back {
    top: 653px;
    background: linear-gradient(180deg, var(--green-mid) 0%, var(--green) 55%, var(--green-deep) 100%);
    color: var(--white);
  }
  .front-wave { position: absolute; left: 0; top: 0; width: 800px; height: 457px; }

  .brand { position: absolute; text-align: center; }
  .brand-mark {
    display: block;
    margin: 0 auto;
    border-radius: 50%;
  }
  .brand-name {
    font-family: "Cinzel", Georgia, serif;
    font-weight: 700;
    font-size: 38px;
    line-height: 1.08;
    white-space: nowrap;
  }
  .front-brand { left: 36px; top: 98px; width: 340px; }
  .front-brand .brand-mark { width: 100px; height: 100px; border: 4px solid var(--gold); }
  .front-brand .brand-name { color: var(--green-deep); margin-top: 16px; }

  .divider-v { position: absolute; width: 1.5px; background: #c9c9c6; }
  .front-divider { left: 383px; top: 72px; height: 300px; }

  .contact { position: absolute; left: 411px; top: 78px; color: var(--ink); }
  .person-name {
    font-family: "Cinzel", Georgia, serif;
    font-weight: 700;
    font-size: 31px;
    color: var(--green-deep);
    letter-spacing: 0.5px;
  }
  .person-role { color: var(--gold); font-size: 18px; line-height: 23px; margin-top: 4px; }
  .address { font-size: 20px; line-height: 25px; margin-top: 12px; }
  .links { list-style: none; margin-top: 10px; font-size: 20px; line-height: 25.5px; }
  .links li { display: flex; align-items: center; gap: 10px; }
  .links svg { width: 18px; height: 18px; fill: var(--green-deep); flex: none; }

  .back-brand { left: 0; top: 40px; width: 800px; }
  .back-brand .brand-mark { width: 100px; height: 100px; border: 5px solid var(--white); }
  .back-brand .brand-name { color: var(--white); margin-top: 16px; }

  .offices {
    position: absolute;
    left: 40px; right: 40px; top: 262px;
    display: grid;
    grid-template-columns: 1fr 1fr 1fr;
    align-items: center;
  }
  .office {
    text-align: center;
    font-size: 15.5px;
    line-height: 19px;
    padding: 10px 0;
  }
  .office + .office { border-left: 1.5px solid rgba(255,255,255,0.75); }
  .office h3 { font-size: 19px; font-weight: 700; margin-bottom: 3px; }
  .office b { font-weight: 700; }
</style>
</head>
<body>

<section class="card card-front" aria-label="Card front">
  <svg class="front-wave" viewBox="0 0 800 457" aria-hidden="true">
    <path d="M0 372 Q400 470 800 372 L800 457 L0 457 Z" fill="var(--gold)"/>
    <path d="M0 380 Q400 480 800 380 L800 457 L0 457 Z" fill="var(--green-deep)"/>
  </svg>

  <div class="brand front-brand">
    <span class="brand-mark" aria-hidden="true"></span>
    <div class="brand-name">HARTWELL<br>LAWYERS</div>
  </div>

  <div class="divider-v front-divider"></div>

  <div class="contact">
    <h1 class="person-name">DANIEL MOREAU</h1>
    <p class="person-role">Director &amp; Principal Solicitor<br>MBA, Juris Doctor</p>
    <p class="address">Level 4, Alder House<br>218 Ridge Terrace<br>Spring Hill, QLD 4000</p>
    <ul class="links">
      <li><svg viewBox="0 0 24 24"><path d="M6.6 10.8a15.2 15.2 0 0 0 6.6 6.6l2.2-2.2c.3-.3.7-.4 1-.2 1.1.4 2.3.6 3.6.6.6 0 1 .4 1 1V20c0 .6-.4 1-1 1A17 17 0 0 1 3 4c0-.6.4-1 1-1h3.5c.6 0 1 .4 1 1 0 1.3.2 2.5.6 3.6.1.3 0 .7-.2 1z"/></svg>+61 7 3000 4172</li>
      <li><svg viewBox="0 0 24 24"><path d="M7 1h10a2 2 0 0 1 2 2v18a2 2 0 0 1-2 2H7a2 2 0 0 1-2-2V3a2 2 0 0 1 2-2zm0 3v14h10V4z"/></svg>+61 0400 123 468</li>
      <li><svg viewBox="0 0 24 24"><path d="M3 6h18v12H3zm1.5 1.5v.6l7.5 5 7.5-5v-.6z"/></svg>daniel@hartwelllawyers.com.au</li>
      <li><svg viewBox="0 0 24 24"><path d="M12 2a10 10 0 1 0 0 20 10 10 0 0 0 0-20zm-1 17.9A8 8 0 0 1 4.1 11L9 15.9V17a2 2 0 0 0 2 2zm6.9-2.5A2 2 0 0 0 16 16h-1v-3a1 1 0 0 0-1-1H8v-2h2a1 1 0 0 0 1-1V7h2a2 2 0 0 0 2-2v-.4a8 8 0 0 1 2.9 12.8z"/></svg>www.hartwelllawyers.com.au</li>
    </ul>
  </div>
</section>

<section class="card card-back" aria-label="Card back">
  <div class="brand back-brand">
    <span class="brand-mark" aria-hidden="true"></span>
    <div class="brand-name">HARTWELL<br>LAWYERS</div>
  </div>

  <div class="offices">
    <div class="office">
      <h3>Melbourne</h3>
      Level 22, 48 Bourke Street<br>Melbourne, VIC 3000<br><b>Phone :</b> +61 039000 1836
    </div>
    <div class="office">
      <h3>Sydney</h3>
      Level 12, Harbour Building<br>74 Church Street<br>Parramatta, NSW 2150<br><b>Phone :</b> +6102 9000 3521
    </div>
    <div class="office">
      <h3>Perth</h3>
      Level 19, Crest Tower<br>212 Murray Terrace<br>Perth, WA 6000<br><b>Phone :</b> +61 08 6000 2957
    </div>
  </div>
</section>

</body>
</html>
```